KDWB Business Card

Looking for a business card design to incorporate our branding. We want to only use the colors listing in the Branding Package (attached).
Updates

Target Market(s)

People who need their phone or device fixed.

Industry/Entity Type

Electronics

Contact Information for Business Card

Please use:

Brightwick Gadget Clinic LLC
4810 E Harlow Ridge Rd
Suite 417
San Antonio, TX 78163

Marcus Delgrove, Store Manager

(210) 555-0147

Requirements
Must have
• Must include the colors that are contained within the Branding Package PDF file.

```html
<!DOCTYPE html>
<html lang="en">
<head>
<meta charset="utf-8">
<title>Brightwick Gadget Clinic – Business Card</title>
<link rel="stylesheet" href="https://fonts.googleapis.com/css2?family=Arimo:wght@400;700&family=Quicksand:wght@500&display=swap">
<style>
  :root {
    --brand-orange: #ef6c00;
    --brand-lime: #c6d73f;
    --card-white: #ffffff;
    --stage-grey: #5a5d5f;
    --band-text: #ffffff;
  }
  * { box-sizing: border-box; margin: 0; padding: 0; }
  html, body {
    width: 1200px;
    height: 804px;
    overflow: hidden;
  }
  body {
    background: var(--stage-grey);
    position: relative;
    font-family: "Arimo", Arial, sans-serif;
  }
  .card {
    position: absolute;
    top: 270px;
    width: 474px;
    height: 264px;
    background: var(--card-white);
    border-radius: 24px;
    overflow: hidden;
  }
  .card--front { left: 108px; }
  .card--back { left: 618px; }

  .brand {
    position: absolute;
    display: flex;
    align-items: center;
    gap: 10px;
  }
  .brand__square {
    width: 40px;
    height: 40px;
    background: var(--brand-orange);
    border-radius: 4px;
    flex: none;
  }
  .brand__name {
    font-family: "Quicksand", "Arimo", sans-serif;
    font-weight: 500;
    color: var(--brand-orange);
    font-size: 18px;
    white-space: nowrap;
  }
  .card--front .brand {
    right: 64px;
    top: 110px;
    justify-content: flex-end;
  }
  .front-tab {
    position: absolute;
    left: 424px;
    top: 110px;
    width: 50px;
    height: 40px;
    background: var(--brand-orange);
    border-radius: 10px 0 0 10px;
  }

  .card--back .brand {
    left: 0;
    right: 0;
    top: 48px;
    justify-content: center;
  }
  .card--back .brand__square { width: 36px; height: 36px; }
  .card--back .brand__name { font-size: 18px; }

  .contact-band {
    position: absolute;
    left: 0;
    right: 0;
    top: 133px;
    height: 108px;
    background: var(--brand-orange);
    color: var(--band-text);
    text-align: center;
    padding-top: 11px;
  }
  .contact-band__name {
    font-weight: 700;
    font-size: 15px;
    letter-spacing: 0.3px;
    line-height: 17px;
  }
  .contact-band__title {
    font-size: 14px;
    line-height: 17px;
  }
  .contact-band__phone {
    font-size: 12.5px;
    margin-top: 9px;
  }
  .contact-band__address {
    font-size: 10.5px;
    margin-top: 13px;
  }
</style>
</head>
<body>
  <section class="card card--front" aria-label="Business card front">
    <div class="brand">
      <span class="brand__square"></span>
      <span class="brand__name">Brightwick Gadget Clinic</span>
    </div>
    <div class="front-tab"></div>
  </section>

  <section class="card card--back" aria-label="Business card back">
    <div class="brand">
      <span class="brand__square"></span>
      <span class="brand__name">Brightwick Gadget Clinic</span>
    </div>
    <div class="contact-band">
      <p class="contact-band__name">MARCUS DELGROVE</p>
      <p class="contact-band__title">Store Manager</p>
      <p class="contact-band__phone">(210) 555-0147</p>
      <p class="contact-band__address">4810 E Harlow Ridge Rd Suite 417 San Antonio,TX 78163</p>
    </div>
  </section>
</body>
</html>
```